Visitenkarten-Design für virtuelle Jobmesse & Jobbörse für Soldaten
Zielgruppe
Die KVL GmbH ist ein Unternehmen das zwei Hauptprodukte betreibt! Zum einen Jobbörse für Soldaten unter www.laufbahnwechsel-beispiel.de und zum anderen eine virtuelle Jobmesse für Soldaten unter www.merivon-beispiel.de , die wir zweimal im Jahr veranstalten.
Aufgabenstellung
Wir haben ja die beiden Produkte Laufbahnwechsel.de und die Merivon, für die bereits jeweils ein separtes Logo besteht! Diese finden Sie im Anhang! Beide werden doch jedoch von einem Unternehmen, der KVL GmbH betrieben! Aktuell nutzen wir eine Visitenkarte mit dem Logo von KVL und eine mit dem Logo der MERIVON. Gerade im Hinblick darauf, dass wir zukünftig auch weiter Plattformen in unser Portfolio aufnehmen, möchte ich hier unsere V-Karten flexibler gestalten!
Ziel soll es also sein, eine Visitenkarte zu gestalten, auf dem klar wird, dass der Mitarbeiter von der KVL GmbH kommt, die KVL GmbH aber unterschiedliche Produkte betreibt.
Im Anhang finden Sie:
1. Das Logo von KVL
2. Das Logo von Merivon
3. Die aktuelle V-Karte von KVL
4. Die aktuelle V-Karte von MERIVON
Vielleicht ein kleiner Anreiz: Aktuell nutzen wir auch zwei getrennte Geschäftspapiere. Das von www.laufbahnwechsel-beispiel.de lade ich einmal hoch! Der Designer, der auch die Visitenkarte erstellt, erhällt im Anschluss den 1:1 Auftrag in Höhe von 200 Euro für die Erstellung des Geschäftspapiers! Wenn Sie jetzt schon einen Vorschlag für das Geschäftspapier einreichen, erhöht das natürlich Ihre Chancen, wobei ich verspreche, dass wir im Falle eine Annahme das 1:1 im Anschluß dennoch starten werden!

```html
<!DOCTYPE html>
<html lang="de">
<head>
<meta charset="utf-8">
<title>Visitenkarten KVL GmbH</title>
<link href="https://fonts.googleapis.com/css2?family=Arimo:wght@400;700&display=swap" rel="stylesheet">
<style>
  :root {
    --blue: #1f4a7c;
    --green: #3f5a2e;
    --text: #555555;
    --border: #8a8a8a;
    --paper: #ffffff;
  }
  * { margin: 0; padding: 0; box-sizing: border-box; }
  html, body { width: 848px; height: 1200px; overflow: hidden; background: var(--paper); }
  body { position: relative; font-family: "Arimo", Arial, sans-serif; color: var(--text); }

  .card {
    position: absolute; width: 342px; height: 221px;
    border: 1px solid var(--border); background: var(--paper); overflow: hidden;
  }
  .card--blue { --brand: var(--blue); }
  .card--green { --brand: var(--green); }

  .card__arc { position: absolute; left: 0; top: 0; width: 342px; height: 221px; }
  .card__arc path { fill: var(--brand); }

  .person { position: absolute; left: 18px; top: 88px; color: #fff; }
  .person__name { font-size: 15px; font-weight: 700; letter-spacing: 0.3px; line-height: 1.1; }
  .person__role { font-size: 11.5px; line-height: 1.4; }

  .logo {
    position: absolute; left: 196px; top: 24px; width: 136px; height: 36px;
    display: flex; align-items: center; justify-content: center; gap: 5px;
    font-size: 10.5px; font-weight: 700; letter-spacing: 0.4px; color: var(--brand);
  }
  .logo__dot { width: 9px; height: 9px; border-radius: 50%; background: var(--brand); }

  .info { position: absolute; top: 0; left: 0; width: 100%; height: 100%; }
  .info > * { position: absolute; white-space: nowrap; line-height: 1; }
  .brand { font-size: 15px; font-weight: 700; color: var(--brand); letter-spacing: 0.2px; }
  .brand--long { font-size: 13.5px; letter-spacing: 0; }
  .tagline { font-size: 9px; color: var(--brand); }
  .line { font-size: 10px; }
  .line--url { font-size: 9px; }
  .line b { font-weight: 700; }

  .icon { position: absolute; left: 161px; width: 15px; height: 15px; }
  .icon * { fill: none; stroke: #666; stroke-width: 1.3; }
</style>
</head>
<body>

<!-- Row 1 : icon variant -->
<div class="card card--blue" style="left:75px; top:198px;">
  <svg class="card__arc" viewBox="0 0 342 221"><path d="M0 0H114C168 55 170 165 103 221H0Z"/></svg>
  <div class="person"><div class="person__name">Jonas Kerber</div><div class="person__role">Position</div></div>
  <div class="logo">LAUFBAHNWECHSEL</div>
  <div class="info">
    <div class="brand brand--long" style="left:183px; top:84px;">Laufbahnwechsel.de</div>
    <div class="tagline" style="left:183px; top:102px;">eine Marke der KVL GmbH</div>
    <div class="line" style="left:183px; top:119px;">Lindenweg 7</div>
    <div class="line" style="left:183px; top:133px;">86999 Falkenau</div>
    <div class="line" style="left:183px; top:152px;">01234 - 567 89 00</div>
    <div class="line" style="left:183px; top:170px;">jonas.kerber@kvl.de</div>
    <div class="line line--url" style="left:183px; top:189px;">www.laufbahnwechsel-beispiel.de</div>
  </div>
  <svg class="icon" style="top:123px" viewBox="0 0 16 16"><path d="M8 15C4 10 3 8 3 6a5 5 0 0 1 10 0c0 2-1 4-5 9Z"/><circle cx="8" cy="6" r="1.8"/></svg>
  <svg class="icon" style="top:148px" viewBox="0 0 16 16"><rect x="4" y="1" width="8" height="14" rx="1.5"/><path d="M7 12.5h2"/></svg>
  <svg class="icon" style="top:169px" viewBox="0 0 16 16"><rect x="1" y="4" width="14" height="9"/><path d="M1 4l7 5 7-5"/></svg>
  <svg class="icon" style="top:187px" viewBox="0 0 16 16"><circle cx="8" cy="8" r="6.5"/><ellipse cx="8" cy="8" rx="3" ry="6.5"/><path d="M1.5 8h13M3 4.5h10M3 11.5h10"/></svg>
</div>

<div class="card card--green" style="left:441px; top:198px;">
  <svg class="card__arc" viewBox="0 0 342 221"><path d="M0 0H114C168 55 170 165 103 221H0Z"/></svg>
  <div class="person"><div class="person__name">Jonas Kerber</div><div class="person__role">Position</div></div>
  <div class="logo"><span class="logo__dot"></span>MERIVON</div>
  <div class="info">
    <div class="brand" style="left:183px; top:83px;">Merivon.de</div>
    <div class="tagline" style="left:183px; top:102px;">eine Marke der KVL GmbH</div>
    <div class="line" style="left:183px; top:119px;">Lindenweg 7</div>
    <div class="line" style="left:183px; top:133px;">86999 Falkenau</div>
    <div class="line" style="left:183px; top:152px;">01234 - 567 89 00</div>
    <div class="line" style="left:183px; top:170px;">jonas.kerber@merivon.de</div>
    <div class="line" style="left:183px; top:188px;">www.merivon-beispiel.de</div>
  </div>
  <svg class="icon" style="top:123px" viewBox="0 0 16 16"><path d="M8 15C4 10 3 8 3 6a5 5 0 0 1 10 0c0 2-1 4-5 9Z"/><circle cx="8" cy="6" r="1.8"/></svg>
  <svg class="icon" style="top:148px" viewBox="0 0 16 16"><rect x="4" y="1" width="8" height="14" rx="1.5"/><path d="M7 12.5h2"/></svg>
  <svg class="icon" style="top:169px" viewBox="0 0 16 16"><rect x="1" y="4" width="14" height="9"/><path d="M1 4l7 5 7-5"/></svg>
  <svg class="icon" style="top:187px" viewBox="0 0 16 16"><circle cx="8" cy="8" r="6.5"/><ellipse cx="8" cy="8" rx="3" ry="6.5"/><path d="M1.5 8h13M3 4.5h10M3 11.5h10"/></svg>
</div>

<!-- Row 2 : labelled variant -->
<div class="card card--blue" style="left:75px; top:464px;">
  <svg class="card__arc" viewBox="0 0 342 221"><path d="M0 0H114C168 55 170 165 103 221H0Z"/></svg>
  <div class="person" style="top:93px;"><div class="person__name">Jonas Kerber</div><div class="person__role">Position</div></div>
  <div class="logo">LAUFBAHNWECHSEL</div>
  <div class="info">
    <div class="brand brand--long" style="left:171px; top:88px;">Laufbahnwechsel.de</div>
    <div class="tagline" style="left:171px; top:106px;">eine Marke der KVL GmbH</div>
    <div class="line" style="left:171px; top:122px;">Lindenweg 7</div>
    <div class="line" style="left:171px; top:137px;">86999 Falkenau</div>
    <div class="line" style="left:171px; top:156px;"><b>T:</b>&nbsp; 01234 - 567 89 00</div>
    <div class="line" style="left:171px; top:174px;"><b>E:</b> jonas.kerber@kvl.de</div>
    <div class="line line--url" style="left:171px; top:189px;"><b>H:</b> www.laufbahnwechsel-beispiel.de</div>
  </div>
</div>

<div class="card card--green" style="left:442px; top:464px;">
  <svg class="card__arc" viewBox="0 0 342 221"><path d="M0 0H114C168 55 170 165 103 221H0Z"/></svg>
  <div class="person" style="top:93px;"><div class="person__name">Jonas Kerber</div><div class="person__role">Position</div></div>
  <div class="logo"><span class="logo__dot"></span>MERIVON</div>
  <div class="info">
    <div class="brand" style="left:171px; top:87px;">Merivon.de</div>
    <div class="tagline" style="left:171px; top:106px;">eine Marke der KVL GmbH</div>
    <div class="line" style="left:171px; top:122px;">Lindenweg 7</div>
    <div class="line" style="left:171px; top:137px;">86999 Falkenau</div>
    <div class="line" style="left:171px; top:156px;"><b>T:</b>&nbsp; 01234 - 567 89 00</div>
    <div class="line" style="left:171px; top:174px;"><b>E:</b> jonas.kerber@kvl.de</div>
    <div class="line line--url" style="left:171px; top:189px;"><b>H:</b> www.laufbahnwechsel-beispiel.de</div>
  </div>
</div>

<!-- Row 3 : plain variant -->
<div class="card card--blue" style="left:75px; top:730px;">
  <svg class="card__arc" viewBox="0 0 342 221"><path d="M0 0H114C168 55 170 165 103 221H0Z"/></svg>
  <div class="person" style="top:93px;"><div class="person__name">Jonas Kerber</div><div class="person__role">Position</div></div>
  <div class="logo">LAUFBAHNWECHSEL</div>
  <div class="info">
    <div class="brand brand--long" style="left:171px; top:89px;">Laufbahnwechsel.de</div>
    <div class="tagline" style="left:171px; top:106px;">eine Marke der KVL GmbH</div>
    <div class="line" style="left:171px; top:124px;">Lindenweg 7</div>
    <div class="line" style="left:171px; top:138px;">86999 Falkenau</div>
    <div class="line" style="left:171px; top:156px;">01234 - 567 89 00</div>
    <div class="line" style="left:171px; top:175px;">jonas.kerber@kvl.de</div>
    <div class="line line--url" style="left:171px; top:189px;">www.laufbahnwechsel-beispiel.de</div>
  </div>
</div>

<div class="card card--green" style="left:442px; top:730px;">
  <svg class="card__arc" viewBox="0 0 342 221"><path d="M0 0H114C168 55 170 165 103 221H0Z"/></svg>
  <div class="person" style="top:93px;"><div class="person__name">Jonas Kerber</div><div class="person__role">Position</div></div>
  <div class="logo"><span class="logo__dot"></span>MERIVON</div>
  <div class="info">
    <div class="brand" style="left:171px; top:88px;">Merivon.de</div>
    <div class="tagline" style="left:171px; top:106px;">eine Marke der KVL GmbH</div>
    <div class="line" style="left:171px; top:124px;">Lindenweg 7</div>
    <div class="line" style="left:171px; top:138px;">86999 Falkenau</div>
    <div class="line" style="left:171px; top:156px;">01234 - 567 89 00</div>
    <div class="line" style="left:171px; top:175px;">jonas.kerber@kvl.de</div>
    <div class="line line--url" style="left:171px; top:189px;">www.laufbahnwechsel-beispiel.de</div>
  </div>
</div>

</body>
</html>
```